Telecommunications/Power civil contractor needs business card design

Were a new telecommunications/power underground civil contractor that is looking for a new business card design. Our company colours are silver or grey and orange. Feel free to use the white background logo or the black background logo.

Target Market(s)

Local contractors, utility companies, private sector mining/energy companies, developers.

Industry/Entity Type

Telecommunications

Contact Information for Business Card

Each card will need the following info:
Persons name:
Title:
E-mail:
Phone number:
Shop Address:
Mailing Address:

Requirements
Must have
• Each card will need the following info:
• Persons name:
• Title:
• E-mail:
• Phone number:
• Shop Address:
• Mailing Address:

```html
<!DOCTYPE html>
<html lang="en">
<head>
<meta charset="utf-8">
<title>Kestrel Line Contracting Inc – Business Card</title>
<link rel="stylesheet" href="https://fonts.googleapis.com/css2?family=Arimo:wght@400;700&display=swap">
<style>
  :root {
    --bg: #2b2b2d;
    --orange: #f05a22;
    --white: #ffffff;
    --card-white: #f7f7f7;
    --grey-dark: #5b5c5e;
    --grey-mid: #8a8b8d;
    --grey-light: #c9c9ca;
    --ink-on-orange: #ffffff;
  }
  * { margin: 0; padding: 0; box-sizing: border-box; }
  html, body {
    width: 1200px; height: 950px; overflow: hidden;
    background: var(--bg);
    font-family: "Arimo", Arial, sans-serif;
  }
  .canvas {
    position: relative; width: 1200px; height: 950px;
  }
  .card {
    position: absolute; left: 250px; width: 700px; height: 400px;
    overflow: hidden; box-shadow: 0 14px 30px rgba(0,0,0,.45);
  }
  /* back side */
  .card-back {
    top: 50px;
    background: linear-gradient(135deg, #7a7b7d 0%, var(--grey-dark) 100%);
    display: flex; align-items: center; justify-content: center;
  }
  .card-back .wordmark { color: var(--grey-light); }
  /* front side */
  .card-front {
    top: 500px; display: flex; background: var(--card-white);
  }
  .contact-panel {
    width: 330px; height: 100%; background: var(--orange);
    color: var(--ink-on-orange); padding: 44px 0 0 38px;
  }
  .person-name { font-weight: 700; font-size: 22px; }
  .person-title { font-size: 15px; margin-top: 4px; }
  .address { font-size: 15px; line-height: 1.35; margin-top: 40px; }
  .contact-list { list-style: none; margin-top: 18px; font-size: 15px; }
  .contact-list li { display: flex; align-items: center; gap: 12px; line-height: 1.6; }
  .contact-list svg { width: 14px; height: 14px; flex: none; }
  .brand-panel {
    flex: 1; display: flex; align-items: center; justify-content: center;
    padding-right: 26px;
  }
  .edge-strip {
    position: absolute; right: 0; top: 0; width: 26px; height: 100%;
    background: var(--grey-mid);
  }
  .brand {
    display: flex; flex-direction: column; align-items: center; gap: 18px;
  }
  .brand-dot {
    width: 84px; height: 84px; border-radius: 50%;
    border: 6px solid var(--grey-mid);
  }
  .card-back .brand-dot { border-color: var(--grey-light); }
  .wordmark {
    font-weight: 700; font-size: 24px; letter-spacing: 1px;
    text-transform: uppercase; color: var(--grey-dark); text-align: center;
    line-height: 1.2;
  }
</style>
</head>
<body>
<div class="canvas">

  <section class="card card-back" aria-label="Business card back">
    <div class="brand">
      <div class="brand-dot"></div>
      <div class="wordmark">Kestrel Line<br>Contracting Inc</div>
    </div>
  </section>

  <section class="card card-front" aria-label="Business card front">
    <div class="contact-panel">
      <div class="person-name">Marcus Hale</div>
      <div class="person-title">President</div>
      <div class="address">2190 Alder Ridge Road<br>Brookhaven, NY 11719</div>
      <ul class="contact-list">
        <li>
          <svg viewBox="0 0 16 16" aria-hidden="true"><path fill="#fff" d="M3 1l3 3-1.5 2c1 2 2.5 3.5 4.5 4.5L11 9l3 3-2 2C6 14 2 10 1 3z"/></svg>
          631 555 0148
        </li>
        <li>
          <svg viewBox="0 0 16 16" aria-hidden="true"><rect x="1" y="3" width="14" height="10" fill="#fff"/><path d="M1 3l7 6 7-6" fill="none" stroke="#f05a22" stroke-width="1.4"/></svg>
          marcus@kestrelline.com
        </li>
        <li>
          <svg viewBox="0 0 16 16" aria-hidden="true"><circle cx="8" cy="8" r="7" fill="#fff"/><path d="M1 8h14M8 1c-3 4-3 10 0 14M8 1c3 4 3 10 0 14" fill="none" stroke="#f05a22" stroke-width="1.1"/></svg>
          www.kestrelline.com
        </li>
      </ul>
    </div>
    <div class="brand-panel">
      <div class="brand">
        <div class="brand-dot"></div>
        <div class="wordmark">Kestrel Line<br>Contracting Inc</div>
      </div>
    </div>
    <div class="edge-strip"></div>
  </section>

</div>
</body>
</html>
```